Every Shelf Set Neatly or ESN Organized needs a business card design. ESN Organized is a professi

We need a business card design that is clean, sharp and conveys a sense of organization. I already have a logo.

Target Market(s)

Families (specifically mothers), small business owners, parents, seniors

Industry/Entity Type

Business

Contact Information for Business Card

My website is www.esnorganized-example.com and my Facebook page is http://www.sociallink-example.com/everyshelfsetneatly. The phone number is 418-552-7094 and I want to be listed as Lorna M. Pelham, Owner

Requirements
Must have
• My logo.

```html
<!DOCTYPE html>
<html lang="en">
<head>
<meta charset="utf-8">
<title>ESN Organized — Business Card</title>
<link href="https://fonts.googleapis.com/css2?family=Source+Sans+3:wght@300;400;600&display=swap" rel="stylesheet">
<style>
  :root {
    --stage: #eef0f2;
    --card-blue: #0a7ddd;
    --frost: #dfe5ea;
    --frost-edge: #c7d0d8;
    --ink-light: #ffffff;
  }
  * { box-sizing: border-box; margin: 0; padding: 0; }
  html, body {
    width: 1200px; height: 900px; overflow: hidden;
    background: var(--stage);
    font-family: "Source Sans 3", "Helvetica Neue", Arial, sans-serif;
  }
  .stage { position: relative; width: 1200px; height: 900px; }
  .card {
    position: absolute;
    background: var(--card-blue);
    color: var(--ink-light);
    overflow: hidden;
    box-shadow: 0 6px 18px rgba(0,0,0,0.12);
  }
  .card-front { left: 78px; top: 35px; width: 588px; height: 363px; }
  .card-back  { left: 388px; top: 505px; width: 565px; height: 350px; }
  .card-accent { position: absolute; inset: 0; width: 100%; height: 100%; }
  .contact-block {
    position: absolute; right: 38px; top: 172px;
    text-align: right;
  }
  .owner-name { font-weight: 600; font-size: 23px; line-height: 1.2; }
  .owner-role { font-weight: 400; font-size: 16px; line-height: 1.2; }
  .contact-list { list-style: none; margin-top: 38px; }
  .contact-list li {
    font-size: 15.5px; line-height: 25px;
    display: flex; justify-content: flex-end; align-items: center; gap: 6px;
  }
  .contact-list svg { width: 12px; height: 12px; fill: var(--ink-light); }
  .brand-name {
    position: absolute; left: 40px; top: 246px; width: 260px;
    text-align: center;
    font-weight: 400; font-size: 30px; line-height: 1;
    color: var(--ink-light);
  }
</style>
</head>
<body>
<main class="stage">

  <section class="card card-front" aria-label="Business card front">
    <svg class="card-accent" viewBox="0 0 588 363" aria-hidden="true">
      <rect x="150" y="-70" width="150" height="420" rx="75" fill="var(--frost)" stroke="var(--frost-edge)" stroke-width="2" transform="rotate(35 225 140)"/>
    </svg>
    <div class="contact-block">
      <p class="owner-name">Lorna M. Pelham</p>
      <p class="owner-role">Owner</p>
      <ul class="contact-list">
        <li>418-552-7094
          <svg viewBox="0 0 24 24"><path d="M6.6 10.8a15 15 0 0 0 6.6 6.6l2.2-2.2a1 1 0 0 1 1-.25 11.4 11.4 0 0 0 3.6.57 1 1 0 0 1 1 1V20a1 1 0 0 1-1 1A17 17 0 0 1 3 4a1 1 0 0 1 1-1h3.5a1 1 0 0 1 1 1c0 1.25.2 2.45.57 3.57a1 1 0 0 1-.25 1z"/></svg>
        </li>
        <li>info@esnorganized-example.com
          <svg viewBox="0 0 24 24"><path d="M2 5h20v14H2z M2 5l10 8 10-8" fill="var(--ink-light)" stroke="var(--card-blue)" stroke-width="1.6"/></svg>
        </li>
        <li>www.esnorganized-example.com
          <svg viewBox="0 0 24 24"><circle cx="12" cy="12" r="10"/><path d="M2 12h20M12 2c3 3 3 17 0 20M12 2c-3 3-3 17 0 20" fill="none" stroke="var(--card-blue)" stroke-width="1.6"/></svg>
        </li>
      </ul>
    </div>
  </section>

  <section class="card card-back" aria-label="Business card back">
    <svg class="card-accent" viewBox="0 0 565 350" aria-hidden="true">
      <rect x="330" y="-40" width="150" height="420" rx="75" fill="var(--frost)" stroke="var(--frost-edge)" stroke-width="2" transform="rotate(-35 405 170)"/>
    </svg>
    <p class="brand-name">ESN Organized</p>
  </section>

</main>
</body>
</html>
```